business card

Business card for new business.
Red and black corporate colors.
Card can have an Indsutrial feel to it. Feel free to add Rust, Bolted steel, or graphics as you see fit. We provide highly specialized services to the below mentioned industries.
Keep information out of corners so that if I want I can choose rounded corners.
Information
- front. name - title - phone - email
- Rear
Refining - Rail - Infrastructure - Mining - Energy
Calgary - Edmonton - Fort McMurray - Revelstoke - Vancouver

```html
<!DOCTYPE html>
<html lang="en">
<head>
<meta charset="utf-8">
<title>Girderline Business Card</title>
<link rel="stylesheet" href="https://fonts.googleapis.com/css2?family=Oswald:wght@500;700&family=Roboto:wght@400&family=Roboto+Condensed:wght@400;700&display=swap">
<style>
  :root {
    --page-bg: #dcd8d3;
    --card-black: #1f2022;
    --frame-grey: #8b8b8b;
    --logo-grey: #808080;
    --brand-red: #e2001a;
    --deep-red: #7c0a14;
    --list-ink: #3b0309;
    --text-light: #f2f2f2;
    --title-grey: #9a9a9a;
  }
  * { box-sizing: border-box; margin: 0; padding: 0; }
  html, body {
    width: 1200px; height: 960px; overflow: hidden;
    background: var(--page-bg);
  }
  .canvas { position: relative; width: 1200px; height: 960px; }

  .card { position: absolute; width: 600px; height: 340px; }
  .card-front { left: 303px; top: 130px; background: var(--card-black); }
  .card-back  { left: 300px; top: 488px; height: 342px; background: var(--brand-red); }

  .card-frame {
    position: absolute; left: 10px; top: 10px; right: 10px; bottom: 10px;
    border: 4px solid var(--frame-grey);
  }
  .card-back .card-frame { border: 5px solid var(--deep-red); }

  .brand-name {
    position: absolute; left: 0; right: 0; top: 86px;
    text-align: center;
    font-family: "Oswald", sans-serif; font-weight: 700;
    font-size: 58px; line-height: 76px; letter-spacing: 1px;
    color: var(--logo-grey);
  }

  .person { position: absolute; right: 331px; top: 198px; text-align: right; }
  .person-name {
    font-family: "Oswald", sans-serif; font-weight: 500;
    font-size: 28px; line-height: 36px; color: var(--brand-red);
  }
  .person-title {
    font-family: "Roboto Condensed", sans-serif; font-weight: 400;
    font-size: 17px; line-height: 20px; color: var(--title-grey);
  }

  .contact { position: absolute; left: 292px; top: 196px; list-style: none; }
  .contact li {
    display: flex; align-items: center; gap: 8px;
    font-family: "Roboto", sans-serif; font-size: 15px; line-height: 19px;
    color: var(--text-light);
  }
  .contact svg { width: 12px; height: 12px; fill: var(--brand-red); flex: none; }

  .brand-square {
    position: absolute; left: 167px; top: 92px;
    width: 108px; height: 108px; background: var(--deep-red);
  }

  .services {
    position: absolute; left: 300px; top: 78px; list-style: none;
    font-family: "Roboto Condensed", sans-serif; font-weight: 700;
    font-size: 14px; line-height: 19px; text-transform: uppercase;
    color: var(--list-ink);
  }
  .services li::before { content: "\2022"; margin-right: 6px; }
</style>
</head>
<body>
<main class="canvas">

  <section class="card card-front" aria-label="Card front">
    <div class="card-frame"></div>
    <div class="brand-name">GIRDERLINE</div>
    <div class="person">
      <div class="person-name">DALE KORVER</div>
      <div class="person-title">CEO/FOUNDER</div>
    </div>
    <ul class="contact">
      <li>
        <svg viewBox="0 0 24 24" aria-hidden="true"><path d="M6.6 10.8a15.1 15.1 0 0 0 6.6 6.6l2.2-2.2c.3-.3.7-.4 1-.2 1.1.4 2.3.6 3.6.6.6 0 1 .4 1 1V20c0 .6-.4 1-1 1A17 17 0 0 1 3 4c0-.6.4-1 1-1h3.5c.6 0 1 .4 1 1 0 1.3.2 2.5.6 3.6.1.3 0 .7-.2 1z"/></svg>
        555 014 2290
      </li>
      <li>
        <svg viewBox="0 0 24 24" aria-hidden="true"><path d="M2 5h20v14H2z M2 5l10 7 10-7" /></svg>
        info@girderline.com
      </li>
      <li>
        <svg viewBox="0 0 24 24" aria-hidden="true"><circle cx="12" cy="12" r="10"/></svg>
        www.girderline.com
      </li>
    </ul>
  </section>

  <section class="card card-back" aria-label="Card back">
    <div class="card-frame"></div>
    <div class="brand-square"></div>
    <ul class="services">
      <li>Refining</li>
      <li>Rail</li>
      <li>Infrastructure</li>
      <li>Mining</li>
      <li>Energy</li>
      <li>Calgary</li>
      <li>Edmonton</li>
      <li>Fort McMurray</li>
      <li>Revelstoke</li>
      <li>Vancouver</li>
    </ul>
  </section>

</main>
</body>
</html>
```